Redesign of business card for Cedar Ridge Mechanical

We are looking for a new design for our business cards for Cedar Ridge Mechanical. We are a plumbing & HVAC construction company, operating on the West Coast of Canada and USA. Logo attached.
Industry/Entity Type
Construction - Plumbing & HVAC
Contact Information for Business Card
Name, address, phone numbers, email, website address
Look and feel
Each slider illustrates characteristics of the customer's brand and the style your logo design should communicate.

```html
<!DOCTYPE html>
<html lang="en">
<head>
<meta charset="utf-8">
<title>Cedar Ridge Mechanical — Business Card</title>
<link rel="stylesheet" href="https://fonts.googleapis.com/css2?family=Poppins:wght@300;400;500;700&display=swap">
<style>
  :root {
    --stage: #232323;
    --card-dark: #212124;
    --card-dark-curve: #1c1c1f;
    --card-light: #e3e4e4;
    --ink-light: #ffffff;
    --ink-muted: #e9e9ea;
    --emboss: #cfd1d1;
  }
  * { box-sizing: border-box; margin: 0; padding: 0; }
  html, body {
    width: 1200px; height: 780px; overflow: hidden;
    background: var(--stage);
    font-family: "Poppins", sans-serif;
  }
  .stage {
    position: relative; width: 1200px; height: 780px;
    display: flex; align-items: center; justify-content: center; gap: 40px;
  }
  .card {
    position: relative; width: 540px; height: 309px; overflow: hidden;
    box-shadow: 0 14px 30px rgba(0,0,0,.45);
  }
  .card--front { background: var(--card-dark); color: var(--ink-light); }
  .card--back  { background: var(--card-light); }

  .front__curve {
    position: absolute; left: 120px; top: -250px;
    width: 430px; height: 430px; border-radius: 50%;
    background: var(--card-dark-curve);
  }
  .front__bar {
    position: absolute; right: 0; top: 22px;
    width: 12px; height: 50px; background: var(--ink-light);
  }
  .identity {
    position: absolute; right: 30px; top: 22px; text-align: right;
  }
  .identity__name { font-size: 30px; line-height: 1.05; letter-spacing: .2px; }
  .identity__first { font-weight: 700; }
  .identity__last { font-weight: 300; }
  .identity__title { font-size: 13px; font-weight: 400; letter-spacing: .4px; margin-top: 2px; }

  .contact {
    position: absolute; right: 30px; top: 130px; text-align: right;
    font-size: 13px; font-weight: 400; line-height: 1.45; color: var(--ink-muted);
  }
  .contact__address { margin-bottom: 8px; }
  .contact__row { display: flex; justify-content: flex-end; align-items: center; gap: 10px; }
  .contact__icon { width: 13px; height: 13px; flex: none; }

  .brand {
    position: absolute; left: 28px; bottom: 28px;
    display: flex; align-items: center; gap: 10px;
  }
  .brand__mark { width: 22px; height: 22px; background: var(--ink-light); }
  .brand__name {
    font-size: 15px; font-weight: 500; letter-spacing: 1.2px;
    text-transform: uppercase; color: var(--ink-light);
  }

  .back__brand {
    position: absolute; inset: 0;
    display: flex; align-items: center; justify-content: center; gap: 16px;
  }
  .back__mark { width: 40px; height: 40px; background: var(--emboss); }
  .back__name {
    font-size: 26px; font-weight: 500; letter-spacing: 2px;
    text-transform: uppercase; color: var(--emboss);
  }
</style>
</head>
<body>
<main class="stage">
  <section class="card card--front" aria-label="Business card front">
    <div class="front__curve"></div>
    <div class="front__bar"></div>
    <header class="identity">
      <p class="identity__name"><span class="identity__first">Marta</span> <span class="identity__last">Kovalova</span></p>
      <p class="identity__title">Founder &amp; CEO</p>
    </header>
    <div class="contact">
      <p class="contact__address">1840 Harbor Ln. Suite 310<br>Port Alder, WA 98301</p>
      <p class="contact__row">(555) 014-2286
        <svg class="contact__icon" viewBox="0 0 16 16" aria-hidden="true"><path fill="#fff" d="M3.6 1.2l2.3 2.6-1.3 1.8a9 9 0 0 0 5.8 5.8l1.8-1.3 2.6 2.3-1.6 2.2C7.6 15.6.4 8.4.9 2.8z"/></svg>
      </p>
      <p class="contact__row">www.cedarridgemech.com
        <svg class="contact__icon" viewBox="0 0 16 16" aria-hidden="true"><circle cx="8" cy="8" r="7" fill="none" stroke="#fff" stroke-width="1.4"/><ellipse cx="8" cy="8" rx="3" ry="7" fill="none" stroke="#fff" stroke-width="1.2"/><path d="M1 8h14" stroke="#fff" stroke-width="1.2"/></svg>
      </p>
      <p class="contact__row">info@cedarridgemech.com
        <svg class="contact__icon" viewBox="0 0 16 16" aria-hidden="true"><rect x="1" y="3" width="14" height="10" fill="none" stroke="#fff" stroke-width="1.4"/><path d="M1 3l7 6 7-6" fill="none" stroke="#fff" stroke-width="1.4"/></svg>
      </p>
    </div>
    <div class="brand">
      <span class="brand__mark"></span>
      <span class="brand__name">Cedar Ridge Mechanical</span>
    </div>
  </section>

  <section class="card card--back" aria-label="Business card back">
    <div class="back__brand">
      <span class="back__mark"></span>
      <span class="back__name">Cedar Ridge Mechanical</span>
    </div>
  </section>
</main>
</body>
</html>
```